NEW Modern Sleek Business Card for VR Language Startup

Our startup is using VR to lead the next wave of world language education. We need a two-sided business card that introduces the larger organization (Brightloom Language Inc) and our contact info on one side and shows the product, Glimwoorld, on the other side.

Side 1 (contact info)= Brightloom Logo and Contact info (name, title, phone, email)

Side 2 (product)= Glimworld logo, text, and website
Text= Culturally Immersive Language Learning Games
Website= www.glimworld-play.com

Target Market(s)

Education, Technology

Contact Information for Business Card

Contact info will be updated upon approval of the design. For now, put this as a placeholder.

Perry Dunmore
Founder & CEO
pdunmore@quillpost-mail.net
(555)-014-2286

Font styles to use
Other font styles liked:
• Gibson and Century Gothic are the brand fonts

Requirements
Nice to have
• I would love to see cohesion between the design and colors of the two logos. I have attached a few business card designs that I like, so you can get a feel for my preferred style.

```html
<!DOCTYPE html>
<html lang="en">
<head>
<meta charset="utf-8">
<title>Brightloom Language – Business Card</title>
<link rel="stylesheet" href="https://fonts.googleapis.com/css2?family=Roboto:ital,wght@0,400;0,500;0,700;1,400;1,500&display=swap">
<style>
  :root {
    --page-bg: #e4e5e8;
    --card-white: #ffffff;
    --card-dark: #1d1f23;
    --pattern-tone-a: #1f2b30;
    --pattern-tone-b: #262a3a;
    --ink-dark: #1a1a1a;
    --ink-light: #ffffff;
    --accent-orange: #ff8a2a;
    --accent-red: #f7354a;
    --accent-purple: #8e45e8;
    --accent-blue: #2bb2f2;
    --accent-cyan: #3fd0f5;
    --rule-blue: #3e63d8;
  }
  * { box-sizing: border-box; margin: 0; padding: 0; }
  html, body {
    width: 1200px; height: 800px; overflow: hidden;
    background: var(--page-bg);
    font-family: "Roboto", Arial, sans-serif;
  }
  .sheet {
    position: relative; width: 1200px; height: 800px;
    display: flex; align-items: center; justify-content: center; gap: 60px;
  }
  .card {
    position: relative; width: 520px; height: 300px; overflow: hidden;
    box-shadow: 0 10px 30px rgba(0,0,0,0.12);
  }

  /* Product side */
  .card--product { background: var(--card-dark); }
  .product-pattern {
    position: absolute; inset: 0;
    background: linear-gradient(135deg, var(--pattern-tone-a), var(--pattern-tone-b) 60%, var(--pattern-tone-a));
    opacity: 0.85;
  }
  .product-brand {
    position: absolute; left: 0; right: 0; top: 92px;
    display: flex; align-items: center; justify-content: center; gap: 12px;
  }
  .brand-dot {
    width: 34px; height: 34px; border-radius: 50%;
    background: var(--accent-cyan);
  }
  .product-name {
    font-size: 40px; font-weight: 500; color: var(--ink-light); letter-spacing: 0.5px;
  }
  .product-tagline {
    position: absolute; left: 0; right: 0; top: 168px; text-align: center;
    font-size: 15px; font-style: italic; font-weight: 500; color: var(--ink-light);
  }
  .product-web {
    position: absolute; left: 0; right: 0; top: 196px;
    display: flex; align-items: center; justify-content: center; gap: 12px;
    font-size: 14px; font-style: italic; color: var(--ink-light);
  }
  .rule { display: flex; align-items: center; width: 110px; }
  .rule-line { flex: 1; height: 1px; background: var(--rule-blue); }
  .rule-node {
    width: 8px; height: 8px; border-radius: 50%;
    border: 1.5px solid var(--rule-blue);
  }

  /* Contact side */
  .card--contact { background: var(--card-white); }
  .contact-wave { position: absolute; inset: 0; }
  .company-brand {
    position: absolute; left: 36px; top: 92px;
    display: flex; align-items: center; gap: 10px;
  }
  .company-dot {
    width: 28px; height: 28px; border-radius: 50%;
    background: var(--accent-purple);
  }
  .company-name {
    font-size: 28px; font-weight: 700; color: var(--ink-dark); letter-spacing: 1px;
  }
  .contact-info {
    position: absolute; right: 28px; top: 150px; text-align: right;
    color: var(--ink-light);
  }
  .contact-name { font-size: 24px; font-weight: 700; line-height: 1.1; }
  .contact-title { font-size: 15px; font-weight: 500; margin-bottom: 16px; }
  .contact-line {
    display: flex; align-items: center; justify-content: flex-end; gap: 8px;
    font-size: 13px; line-height: 1.7;
  }
  .contact-line svg { width: 12px; height: 12px; fill: var(--ink-dark); }
</style>
</head>
<body>
<main class="sheet">

  <section class="card card--product">
    <div class="product-pattern" role="img" aria-label="Faint repeating pattern of the product symbol across a dark background"></div>
    <div class="product-brand">
      <span class="brand-dot"></span>
      <span class="product-name">Glimworld</span>
    </div>
    <p class="product-tagline">Culturally Immersive Language Learning Games</p>
    <div class="product-web">
      <span class="rule"><span class="rule-line"></span><span class="rule-node"></span></span>
      <span>www.glimworld-play.com</span>
      <span class="rule"><span class="rule-node"></span><span class="rule-line"></span></span>
    </div>
  </section>

  <section class="card card--contact">
    <svg class="contact-wave" viewBox="0 0 520 300" width="520" height="300" aria-hidden="true">
      <defs>
        <linearGradient id="waveGradient" x1="1" y1="0" x2="0.2" y2="1">
          <stop offset="0" stop-color="#ff8a2a"/>
          <stop offset="0.35" stop-color="#f7354a"/>
          <stop offset="0.7" stop-color="#8e45e8"/>
          <stop offset="1" stop-color="#2bb2f2"/>
        </linearGradient>
      </defs>
      <path fill="url(#waveGradient)" d="M362 0 C302 0 292 60 282 120 C267 210 222 270 172 300 L520 300 L520 0 Z"/>
      <path fill="#ffffff" d="M372 0 C312 0 302 60 292 120 C277 210 232 270 182 300 L520 300 L520 0 Z"/>
      <path fill="url(#waveGradient)" d="M380 0 C320 0 310 60 300 120 C285 210 240 270 190 300 L520 300 L520 0 Z"/>
    </svg>
    <div class="company-brand">
      <span class="company-dot"></span>
      <span class="company-name">Brightloom</span>
    </div>
    <div class="contact-info">
      <p class="contact-name">Perry Dunmore</p>
      <p class="contact-title">Founder &amp; CEO</p>
      <p class="contact-line">(555)-014-2286
        <svg viewBox="0 0 24 24"><path d="M6.6 10.8a15 15 0 0 0 6.6 6.6l2.2-2.2a1 1 0 0 1 1-.25 11.4 11.4 0 0 0 3.6.57 1 1 0 0 1 1 1V20a1 1 0 0 1-1 1A17 17 0 0 1 3 4a1 1 0 0 1 1-1h3.5a1 1 0 0 1 1 1c0 1.250.2 2.450.57 3.57a1 1 0 0 1-.25 1z"/></svg>
      </p>
      <p class="contact-line">pdunmore@quillpost-mail.net
        <svg viewBox="0 0 24 24"><path d="M2 5h20v14H2z M2 5l10 8 10-8" fill="none" stroke="#1a1a1a" stroke-width="2"/></svg>
      </p>
    </div>
  </section>

</main>
</body>
</html>
```